Simple Recipe eBook

I need the graphic work done for a simple recipe ebook, I have attached all of the required information for it, as well as our company logo. Further company info can be found at velorabix.com

I would like each recipe page to include 2 recipes, each recipe needs to include ingredients, picture, method, and nutritional info.

I would like the style to appear fresh and healthy, with lots of graphics and colours to match.
Please let me know if you need any guidance

Target Market(s)

Females aged from 15-25

Industry/Entity Type

It Company

```html
<!DOCTYPE html>
<html lang="en">
<head>
<meta charset="utf-8">
<title>Velorabix Detox &amp; Diet Guide – Dos</title>
<link rel="stylesheet" href="https://fonts.googleapis.com/css2?family=Arvo:wght@400;700&family=Work+Sans:wght@300;400&family=Open+Sans:wght@700;800&display=swap">
<style>
  :root {
    --canvas: #ebebeb;
    --page: #ffffff;
    --leaf: #96c34a;
    --lime: #8dc63f;
    --forest: #0c6a37;
    --ink: #5a5a5a;
    --white: #ffffff;
  }
  * { box-sizing: border-box; margin: 0; padding: 0; }
  html, body { width: 1200px; height: 1000px; overflow: hidden; background: var(--canvas); }
  .canvas { position: relative; width: 1200px; height: 1000px; }

  .spread { position: absolute; left: 84px; top: 148px; width: 1031px; height: 729px; display: flex; }
  .page-intro { position: relative; width: 516px; height: 100%; background: var(--page); }
  .page-dos { position: relative; width: 515px; height: 100%; background: var(--leaf); }

  .intro-lead {
    position: absolute; left: 47px; top: 44px; width: 420px;
    font-family: "Work Sans", sans-serif; font-weight: 400; font-size: 13.5px; line-height: 18px; color: var(--ink);
  }
  .intro-mission {
    position: absolute; left: 47px; top: 88px;
    font-family: "Arvo", serif; font-size: 16.5px; line-height: 22px; color: var(--lime); text-transform: uppercase; letter-spacing: 0.3px;
  }
  .intro-note {
    position: absolute; left: 47px; top: 143px; width: 420px;
    font-family: "Work Sans", sans-serif; font-size: 12.5px; line-height: 16px; color: var(--ink);
  }
  .intro-title {
    position: absolute; left: 46px; top: 176px;
    font-family: "Arvo", serif; font-weight: 700; color: var(--lime); white-space: nowrap; letter-spacing: 0.5px;
  }
  .intro-title .big { font-size: 46px; }
  .intro-title .small { font-size: 34px; }

  .icon-cluster { position: absolute; left: 0; top: 0; width: 516px; height: 729px; }
  .goal-word { font-family: "Open Sans", sans-serif; font-weight: 800; font-size: 24px; fill: var(--white); }
  .goal-line { font-family: "Open Sans", sans-serif; font-weight: 700; font-size: 15px; fill: var(--white); }

  .dos-title {
    position: absolute; left: 53px; top: 70px;
    font-family: "Arvo", serif; font-weight: 700; font-size: 48px; color: var(--white); letter-spacing: 1px;
  }
  .dos-mark { position: absolute; right: 0; top: 75px; width: 62px; height: 53px; background: var(--forest); }
  .dos-mark svg { display: block; }

  .dos-list { position: absolute; left: 53px; top: 184px; width: 440px; list-style: none; }
  .dos-item { margin-bottom: 10px; }
  .dos-item h2 {
    font-family: "Arvo", serif; font-weight: 400; font-size: 12.5px; line-height: 17px; color: var(--forest); text-transform: uppercase; letter-spacing: 0.4px;
  }
  .dos-item p {
    font-family: "Work Sans", sans-serif; font-weight: 300; font-size: 10.6px; line-height: 14px; color: var(--white);
  }
</style>
</head>
<body>
<div class="canvas">
  <div class="spread">
    <section class="page-intro">
      <p class="intro-lead">At Velorabix we want to help you be the best you can be!<br>That’s why we have put together this simple guide</p>
      <p class="intro-mission">To motivate, inspire, inform,<br>and help you reach your goals.</p>
      <p class="intro-note">Below you will find a collection of healthy and easy recipe ideas<br>and tips to kickstart your detox and diet journey.</p>
      <h1 class="intro-title"><span class="big">READY?</span> <span class="small">SET....GO!</span></h1>

      <svg class="icon-cluster" viewBox="0 0 516 729" xmlns="http://www.w3.org/2000/svg">
        <circle cx="184" cy="350" r="60" fill="var(--forest)" role="img" aria-label="Bicycle icon for exercise"/>
        <circle cx="329" cy="350" r="60" fill="var(--lime)" role="img" aria-label="Scale gauge icon for counting calories"/>
        <circle cx="119" cy="478" r="60" fill="var(--lime)" role="img" aria-label="Two friends high-fiving icon"/>
        <g role="img" aria-label="Goal list">
          <circle cx="259" cy="478" r="60" fill="var(--lime)"/>
          <text class="goal-word" x="259" y="461" text-anchor="middle">GOAL!</text>
          <text class="goal-line" x="220" y="483">1............</text>
          <text class="goal-line" x="220" y="500">2............</text>
          <text class="goal-line" x="220" y="517">3............</text>
        </g>
        <circle cx="397" cy="478" r="60" fill="var(--forest)" role="img" aria-label="Glass and water bottles icon"/>
        <circle cx="184" cy="602" r="60" fill="var(--forest)" role="img" aria-label="Melon slice and carrot icon"/>
        <circle cx="329" cy="602" r="60" fill="var(--lime)" role="img" aria-label="Person sleeping in bed icon"/>
      </svg>
    </section>

    <section class="page-dos">
      <h1 class="dos-title">DOS</h1>
      <div class="dos-mark">
        <svg width="62" height="53" viewBox="0 0 62 53" xmlns="http://www.w3.org/2000/svg" role="img" aria-label="Tick">
          <path d="M17 27 L27 40 L45 11" fill="none" stroke="var(--white)" stroke-width="5" stroke-linecap="round" stroke-linejoin="round"/>
        </svg>
      </div>
      <ul class="dos-list">
        <li class="dos-item"><h2>Exercise!</h2><p>Exercise is the key to achieving your goals. Aim for at least 30 minutes<br>of high intensity cardio or weight training each day</p></li>
        <li class="dos-item"><h2>Count your calories!</h2><p>To be sure you aren’t eating too much you should make sure to count your calories.<br>Download an app like CalorieTrail to help you keep track on the go.<br>The app will also help decide how many calories you should be consuming per day.</p></li>
        <li class="dos-item"><h2>Drink plenty of water!</h2><p>Staying hydrated is important to keep your body functioning at its peak.<br>A glass of water before each meal can help you feel fuller quicker.<br>It also helps flush nasty toxins.</p></li>
        <li class="dos-item"><h2>Get a goodnight sleep!</h2><p>Your beauty rest is important to help your body repair.<br>6-8 hours every night is recommended.</p></li>
        <li class="dos-item"><h2>Write down your goals!</h2><p>Did you know that writing down your goals increases your chance of actually<br>completing them? It does! Give it a go. Write them down and stick to them.<br>Hard work and consistency pays off!</p></li>
        <li class="dos-item"><h2>Eat fruit &amp; veggies!</h2><p>Fresh fruit and veges are loaded with healthy vitamins and antioxidants<br>that your body loves!</p></li>
        <li class="dos-item"><h2>Do it with a friend!</h2><p>Doing your diet and detox with a friend can be a great way to boost motivation<br>and get results. Keep each other on track and share ideas.</p></li>
      </ul>
    </section>
  </div>
</div>
</body>
</html>
```